Need help in designing new business card utilizing our new logo.

BuildMark Solutions works with Construction Business Owners, Managers & IT Professionals to strengthen software usage and increase user productivity.

Our Construction Accounting and Mobile Field Management Software Clients engage with us in the following areas:

New Software Implementations
Software Re-Implementations
Redesigning Software Usage at the User Level
Project Coordination & Management
Continued Software Support

Old tag line:
Weighing Options - Implementing Solutions

www.buildmark-solutions.example

Ridge 4 is a product, but not needed for a new business card.

```html
<!DOCTYPE html>
<html lang="en">
<head>
<meta charset="utf-8">
<title>BuildMark Solutions — Business Card</title>
<link rel="stylesheet" href="https://fonts.googleapis.com/css2?family=Montserrat:wght@400;500;600&display=swap">
<style>
  :root {
    --backdrop: #222222;
    --card-white: #ffffff;
    --card-dark: #181818;
    --brand-blue: #2b2f9c;
    --brand-grey: #c4c4c8;
    --text-grey: #555559;
    --text-light: #f2f2f2;
  }
  * { box-sizing: border-box; margin: 0; padding: 0; }
  html, body {
    width: 1200px; height: 897px; overflow: hidden;
    background: var(--backdrop);
    font-family: "Montserrat", sans-serif;
  }
  .card {
    position: absolute; left: 303px; width: 595px; height: 339px;
    border-radius: 19px; overflow: hidden;
    box-shadow: 0 6px 18px rgba(0,0,0,.45);
  }
  .card--front { top: 92px; background: var(--card-white); }
  .card--back { top: 470px; background: var(--card-dark); }

  .swoop { position: absolute; inset: 0; width: 595px; height: 339px; }

  .brand {
    position: absolute; display: flex; align-items: center; gap: 10px;
    color: var(--brand-blue); font-weight: 600; white-space: nowrap;
  }
  .brand__square { background: var(--brand-blue); flex: none; }
  .card--front .brand { left: 31px; top: 68px; font-size: 26px; }
  .card--front .brand__square { width: 20px; height: 20px; }
  .card--back .brand { left: 0; right: 0; justify-content: center; top: 118px; font-size: 34px; }
  .card--back .brand__square { width: 26px; height: 26px; }

  .tagline {
    position: absolute; left: 31px; top: 120px;
    color: var(--brand-blue); font-size: 15px; font-weight: 500; line-height: 20px;
  }
  .person { position: absolute; right: 30px; top: 30px; text-align: right; }
  .person__name { color: var(--brand-blue); font-size: 22px; font-weight: 600; line-height: 28px; }
  .person__role { color: var(--text-grey); font-size: 14px; line-height: 16px; }
  .accent-bar { position: absolute; right: 0; top: 36px; width: 16px; height: 40px; background: var(--brand-blue); }

  .address {
    position: absolute; right: 30px; top: 181px; text-align: right;
    color: var(--text-light); font-size: 14.5px; line-height: 20px;
  }
  .contacts { position: absolute; right: 28px; top: 236px; list-style: none; }
  .contacts li {
    display: flex; justify-content: flex-end; align-items: center; gap: 9px;
    color: var(--text-light); font-size: 14.5px; line-height: 20px;
  }
  .contacts svg { width: 11px; height: 11px; flex: none; }
  .contacts .hl { color: var(--brand-blue); }

  .services {
    position: absolute; left: 0; right: 0; top: 234px; text-align: center;
    color: var(--text-light); font-size: 14.5px; line-height: 20.5px;
  }
</style>
</head>
<body>
  <section class="card card--front">
    <svg class="swoop" viewBox="0 0 595 339" aria-hidden="true">
      <path d="M0 332 C120 210 360 148 595 148 L595 339 L0 339 Z" fill="var(--brand-blue)"/>
      <path d="M14 339 C140 218 370 152 595 151 L595 339 Z" fill="var(--brand-grey)"/>
      <path d="M44 339 C170 226 380 156 595 152 L595 339 Z" fill="var(--card-dark)"/>
    </svg>

    <div class="brand"><span class="brand__square"></span>BuildMark Solutions</div>
    <p class="tagline">Construction Accounting<br>Software Consultants</p>

    <div class="person">
      <p class="person__name">Dana R. Whitfield</p>
      <p class="person__role">Owner</p>
    </div>
    <span class="accent-bar"></span>

    <p class="address">48 Maple Avenue Suite 112<br>Glenridge NY 12000</p>
    <ul class="contacts">
      <li>800-555-0142 ext.100
        <svg viewBox="0 0 12 12"><path d="M3 1 L5 3.5 L4 5 Q5 7 7 8 L8.5 7 L11 9 L9.5 11 Q4 10.5 1 3 Z" fill="var(--brand-blue)"/></svg></li>
      <li>518-555-0193
        <svg viewBox="0 0 12 12"><rect x="3" y="0.8" width="6" height="10.4" rx="1" fill="none" stroke="var(--brand-blue)" stroke-width="1.3"/></svg></li>
      <li>dana.whitfield@buildmark-solutions.example
        <svg viewBox="0 0 12 12"><rect x="1" y="2.5" width="10" height="7" fill="none" stroke="var(--brand-blue)" stroke-width="1.2"/><path d="M1 2.5 L6 6.5 L11 2.5" fill="none" stroke="var(--brand-blue)" stroke-width="1.2"/></svg></li>
      <li><span>www.<span class="hl">buildmark-solutions</span>.example</span>
        <svg viewBox="0 0 12 12"><circle cx="6" cy="6" r="5" fill="none" stroke="var(--brand-blue)" stroke-width="1.2"/><ellipse cx="6" cy="6" rx="2" ry="5" fill="none" stroke="var(--brand-blue)" stroke-width="1"/><path d="M1 6 H11" stroke="var(--brand-blue)" stroke-width="1"/></svg></li>
    </ul>
  </section>

  <section class="card card--back">
    <div class="brand"><span class="brand__square"></span>BuildMark Solutions</div>
    <p class="services">
      New Software Implementations | Software Re-Implementations<br>
      Redesigning Software Usage at the User Level<br>
      Project Coordination &amp; Management<br>
      Continued Software Support
    </p>
  </section>
</body>
</html>
```